Website for Vornelix Capital, my new firm that raises money from investors to buy, build, own an...

Vornelix Capital needs a website! We are a new company with very experienced people, who invest in, own and build hotel properties, as well as apartments and other commercial real estate. We seek investors for our projects, and we provide safe, secure returns on their investment in our projects. Our new logo is designed to exhibit strength, class and security, and would like our website to continue on this theme. Our name, Vornelix, is a word-play on a Greek word “aristeia”, which means “excellence” and “a warriors finest moment of glory in war”. If you are in business, you realize that much of it is like war, with strategy and moves and opponents and competitors, and ever-changing economic conditions and threats that make business very much like war. We like to think that we are good at business (war), and so have named our company “Vornelix”, using the founders last name and the word “aristeia” combined. Another definition of "aristeia" is "performing at the peak of one's potential after a long struggle"...again, much like business in real life! The website design should exhibit financial security, smart moves, and positive growth towards a bright future.

Target Market(s)

The target market is smart and wealthy investors, with others such as brokers, cities and government agencies, lenders, sellers, partners, etc also looking at it.

Industry/Entity Type

Investment

Number of Pages Required

5+ page

Font styles to use
Sans Serif

Colors
fec214

Requirements
Must have
• Our website should have a landing page, a "about" or bio page, a projects page and a contact us page. Our new logo uses the colors black and gold, so this should be factored in to our site. The site should be simple, yet impactful and impressive. I have actually two logos, which can be mixed and interchanged in a complimentary way, each with their own unique look.
Nice to have
• I have uploaded a couple screenshots of a website i like, and the simplicity I mention.
Should not have
• The site should not be flashy or complicated or complex or "busy"

```html
<!DOCTYPE html>
<html lang="en">
<head>
<meta charset="utf-8">
<title>Vornelix Capital</title>
<link href="https://fonts.googleapis.com/css2?family=Lato:wght@400;700;900&display=swap" rel="stylesheet">
<style>
:root{
  --gold:#c9a13b;
  --gold-bright:#fec214;
  --ink:#1b1b1b;
  --white:#ffffff;
  --paper:#f4f4f2;
  --footer:#141414;
}
*{margin:0;padding:0;box-sizing:border-box}
html,body{width:1200px;height:4832px;overflow:hidden}
body{font-family:'Lato',sans-serif;color:var(--ink);background:var(--white);position:relative}
section,header,footer{position:absolute;left:0;width:1200px}
.center{text-align:center}
.eyebrow{font-weight:700;font-size:22px;letter-spacing:1px;text-transform:uppercase}
.rule{display:block;width:84px;height:4px;background:var(--gold);margin:14px auto 0}
.body-copy{font-size:17px;line-height:24px;font-weight:700}
.btn{position:absolute;display:flex;align-items:center;justify-content:center;font-weight:700;font-size:19px;letter-spacing:1px;text-transform:uppercase;border:3px solid var(--ink);height:44px}

/* Nav */
.site-nav{top:0;height:88px;background:var(--white)}
.brand{position:absolute;left:168px;top:26px;display:flex;align-items:center;gap:10px;font-size:26px;font-weight:700;color:#333;text-transform:uppercase;letter-spacing:1px}
.brand-mark{width:14px;height:14px;background:var(--gold)}
.brand-line{position:absolute;left:120px;top:84px;width:290px;height:4px;background:var(--gold)}
.nav-links{position:absolute;right:176px;top:36px;display:flex;gap:30px;font-size:17px;font-weight:900;letter-spacing:.5px}

/* Hero */
.hero{top:88px;height:700px;color:var(--white)}
.hero-photo{position:absolute;inset:0;background:linear-gradient(180deg,#4a6684 0%,#2f4763 45%,#1e2f44 100%)}
.hero-tab{position:absolute;left:472px;bottom:0;width:256px;height:16px;background:#8b8f94}
.hero-text{position:absolute;top:140px;width:100%}
.hero-title{font-size:46px;line-height:58px;font-weight:700;margin-top:50px}
.hero-copy{width:560px;margin:34px auto 0}
.hero-chevron{position:absolute;left:570px;top:588px}

/* Projects */
.projects{top:788px;height:692px;background:var(--white)}
.projects-title{position:absolute;top:100px;width:100%;font-size:32px;font-weight:900}
.service{position:absolute;top:212px;width:180px;text-align:center;font-weight:900;font-size:16px}
.service svg{display:block;margin:0 auto 42px}

/* Protection */
.protection{top:1480px;height:700px}
.protection-photo{position:absolute;left:0;top:0;width:1200px;height:650px;background:linear-gradient(135deg,#8a8a8a,#c7c7c7 40%,#6d6d6d 75%,#a9a9a9)}
.protection-panel{position:absolute;left:172px;top:148px;width:856px;height:552px;background:rgba(45,45,45,.82);color:var(--white);overflow:hidden}
.protection-panel .accent{position:absolute;left:0;bottom:0;width:856px;height:70px;background:var(--gold);clip-path:polygon(0 0,100% 55%,100% 100%,0 100%)}
.protection-text{position:absolute;top:72px;width:100%}
.protection-title{font-size:38px;line-height:48px;font-weight:700;margin-top:30px}

/* About */
.about{top:2180px;height:780px;background:var(--white)}
.about-text{position:absolute;top:104px;width:100%}
.quote{font-size:40px;line-height:50px;font-weight:900;margin-top:30px}
.about-copy{width:660px;margin:36px auto 0}
.founder{margin-top:40px;font-weight:900;font-size:20px}
.founder-role{color:var(--gold);font-weight:900;font-size:13px;letter-spacing:1px;margin-top:6px}

/* Smart move */
.smart{top:2960px;height:812px;color:var(--white)}
.smart-photo{position:absolute;inset:0;background:linear-gradient(180deg,#2b2b2b 0%,#4a4a4a 55%,#7a7a7a 100%)}
.smart-text{position:absolute;top:134px;width:100%}
.smart-title{font-size:42px;line-height:50px;font-weight:700;margin-top:30px}
.smart-copy{width:660px;margin:34px auto 0}

/* Future */
.future{top:3772px;height:828px;color:var(--white)}
.future-photo{position:absolute;inset:0;background:linear-gradient(180deg,#7f7a4c 0%,#948b50 45%,#b28a3a 75%,#5a3d1f 100%)}
.future-text{position:absolute;top:120px;width:100%}
.future-title{font-size:40px;line-height:50px;font-weight:700;margin-top:66px}
.future-copy{width:660px;margin:28px auto 0}

/* Footer */
.site-footer{top:4600px;height:232px;background:var(--footer);color:var(--white)}
.address{position:absolute;left:188px;top:30px;font-size:17px;line-height:22px;font-weight:700}
.copyright{position:absolute;left:188px;top:140px;font-size:12px;font-weight:700}
.badge{position:absolute;left:636px;top:24px;width:78px;height:58px;background:#e9e9e9}
.social{position:absolute;left:636px;top:116px;display:flex;gap:32px}
.social span{width:24px;height:24px;border-radius:50%;background:var(--white)}
</style>
</head>
<body>

<header class="site-nav">
  <div class="brand"><span class="brand-mark"></span>Vornelix Capital</div>
  <span class="brand-line"></span>
  <nav class="nav-links"><span>ABOUT US</span><span>PROJECT</span><span>FINANCE</span><span>CONTACT</span></nav>
</header>

<section class="hero">
  <div class="hero-photo" role="img" aria-label="Looking up at a glass office tower against a blue sky"></div>
  <div class="hero-text center">
    <div class="eyebrow">The Gold of Management Capital</div>
    <svg width="30" height="28" style="display:block;margin:26px auto 0" aria-hidden="true"><rect x="4" y="2" width="4" height="24" fill="#c9a13b"/><rect x="13" y="2" width="4" height="24" fill="#c9a13b"/><rect x="22" y="2" width="4" height="24" fill="#c9a13b"/></svg>
    <h1 class="hero-title" style="margin-top:26px">Performing at the peak of one’s<br>potential after a long struggle</h1>
    <p class="body-copy hero-copy">Lorem ipsum dolor sit amet, consectetur adipiscing elit. Donec pretium nisi malesuada porttitor iaculis. Suspendisse molestie nec sem sed placerat. Nam massa tellus, blandit sed egestas cursus, lacinia id purus. Donec pretium nisi malesuada porttitor iaculis.</p>
  </div>
  <svg class="hero-chevron" width="60" height="30" aria-hidden="true"><polyline points="4,4 30,26 56,4" fill="none" stroke="#c9a13b" stroke-width="6"/></svg>
  <span class="hero-tab"></span>
</section>

<section class="projects">
  <h2 class="projects-title center">PROJECT WITH US<span class="rule"></span></h2>
  <div class="service" style="left:158px">
    <svg width="140" height="140" aria-hidden="true"><circle cx="70" cy="70" r="70" fill="#c9a13b"/><circle cx="70" cy="70" r="58" fill="none" stroke="#fff" stroke-width="4"/><circle cx="70" cy="70" r="26" fill="none" stroke="#fff" stroke-width="6"/><text x="70" y="81" text-anchor="middle" font-family="Lato,sans-serif" font-weight="900" font-size="30" fill="#fff">$</text></svg>
    INVESMENT
  </div>
  <div class="service" style="left:394px">
    <svg width="140" height="140" aria-hidden="true"><circle cx="70" cy="70" r="70" fill="#c9a13b"/><circle cx="70" cy="70" r="58" fill="none" stroke="#fff" stroke-width="4"/><rect x="42" y="78" width="12" height="20" fill="#fff"/><rect x="60" y="66" width="12" height="32" fill="#fff"/><rect x="78" y="54" width="12" height="44" fill="#fff"/><polyline points="40,66 60,52 76,44 96,34" fill="none" stroke="#fff" stroke-width="4"/></svg>
    FINANCE
  </div>
  <div class="service" style="left:630px">
    <svg width="140" height="140" aria-hidden="true"><circle cx="70" cy="70" r="70" fill="#c9a13b"/><circle cx="70" cy="70" r="58" fill="none" stroke="#fff" stroke-width="4"/><rect x="46" y="36" width="34" height="64" fill="#fff"/><rect x="53" y="44" width="7" height="7" fill="#c9a13b"/><rect x="66" y="44" width="7" height="7" fill="#c9a13b"/><rect x="53" y="58" width="7" height="7" fill="#c9a13b"/><rect x="66" y="58" width="7" height="7" fill="#c9a13b"/><circle cx="90" cy="86" r="14" fill="#fff" stroke="#c9a13b" stroke-width="3"/><text x="90" y="92" text-anchor="middle" font-family="Lato,sans-serif" font-weight="900" font-size="16" fill="#c9a13b">$</text></svg>
    PROPERTY
  </div>
  <div class="service" style="left:862px">
    <svg width="140" height="140" aria-hidden="true"><circle cx="70" cy="70" r="70" fill="#c9a13b"/><circle cx="70" cy="70" r="58" fill="none" stroke="#fff" stroke-width="4"/><polygon points="70,36 102,66 38,66" fill="#fff"/><rect x="46" y="64" width="48" height="36" fill="#fff"/><rect x="63" y="78" width="14" height="22" fill="#c9a13b"/></svg>
    REAL ESTATE
  </div>
  <span class="btn" style="left:440px;top:572px;width:320px">How to get started</span>
</section>

<section class="protection">
  <div class="protection-photo" role="img" aria-label="Black and white photo of a padlock resting on rolled banknotes"></div>
  <div class="protection-panel">
    <div class="accent"></div>
    <div class="protection-text center">
      <div class="eyebrow">Secure and Protection<span class="rule"></span></div>
      <h2 class="protection-title">Reliable investment protection<br>with accurate and always refined analysis<br>information technology</h2>
    </div>
    <span class="btn" style="left:328px;top:364px;width:204px;border-color:#fff;color:#fff">Learn more</span>
  </div>
</section>

<section class="about">
  <div class="about-text center">
    <div class="eyebrow">About Us<span class="rule"></span></div>
    <h2 class="quote">" Building commitment and communication<br>has a strong meaning in building<br>a sustainable business "</h2>
    <p class="body-copy about-copy">Lorem ipsum dolor sit amet, consectetur adipiscing elit. Donec pretium nisi malesuada porttitor iaculis. Suspendisse molestie nec sem sed placerat. Nam massa tellus, blandit sed egestas cursus, lacinia id purus</p>
    <div class="founder">MARCUS VELL</div>
    <div class="founder-role">FOUNDER</div>
  </div>
  <span class="btn" style="left:520px;top:600px;width:160px">Our team</span>
</section>

<section class="smart">
  <div class="smart-photo" role="img" aria-label="Black and white photo of a hand moving a piece on a chessboard"></div>
  <div class="smart-text center">
    <div class="eyebrow">A Smart Move<span class="rule"></span></div>
    <h2 class="smart-title">Challenge after challenge in the era of<br>economic war made us strong in running<br>a business with vairous strategies<br>that worked appropriately</h2>
    <p class="body-copy smart-copy">Lorem ipsum dolor sit amet, consectetur adipiscing elit. Donec pretium nisi malesuada porttitor iaculis. Suspendisse molestie nec sem sed placerat. Nam massa tellus, blandit sed egestas cursus, lacinia id purus</p>
  </div>
  <span class="btn" style="left:500px;top:640px;width:204px;border-color:var(--gold);color:var(--gold)">Learn more</span>
</section>

<section class="future">
  <div class="future-photo" role="img" aria-label="Silhouetted group standing in a field at golden sunset"></div>
  <div class="future-text center">
    <div class="eyebrow">Invesment for the Future<span class="rule"></span></div>
    <h2 class="future-title">We and you will always see a lot of<br>opportunities in every challenge by opening<br>the space to coma out staring ahead<br>that is more cheerful</h2>
    <p class="body-copy future-copy">Lorem ipsum dolor sit amet, consectetur adipiscing elit. Donec pretium nisi malesuada porttitor iaculis. Suspendisse molestie nec sem sed placerat. Nam massa tellus, blandit sed egestas cursus, lacinia id purus</p>
  </div>
  <span class="btn" style="left:332px;top:664px;width:208px;background:var(--gold);border-color:var(--gold);color:#fff">Join us</span>
  <span class="btn" style="left:660px;top:664px;width:212px;border-color:#fff;color:#fff">Contact us</span>
</section>

<footer class="site-footer">
  <div class="address">Orrin Gold Street 214<br>Halden City, USA<br>T. +1 555 014 2290</div>
  <div class="copyright">©2018 Vornelix All Right Reserved</div>
  <div class="badge" aria-label="Partner badge"></div>
  <div class="social" aria-label="Social links"><span></span><span></span><span></span><span></span><span></span><span></span></div>
</footer>

</body>
</html>
```